Business card design for my company.
I would like the card's background colour to be black. You can also see our web site to get an idea of our brand. https://www.tmwhomecrafting.com.au/
- Name
- Email

```html
<!DOCTYPE html>
<html lang="en">
<head>
<meta charset="utf-8">
<title>TMW Home Crafting – Business Card</title>
<link href="https://fonts.googleapis.com/css2?family=Jost:wght@400;500;700&display=swap" rel="stylesheet">
<style>
  :root {
    --stage: #2b2b2d;
    --card-black: #0a0a0a;
    --green-light: #4fae45;
    --green-mid: #2f9a43;
    --green-deep: #178a3f;
    --white: #f4f4f4;
    --ink: #0b0b0b;
  }
  * { box-sizing: border-box; margin: 0; padding: 0; }
  html, body { width: 1200px; height: 900px; overflow: hidden; }
  body {
    background: var(--stage);
    font-family: "Jost", sans-serif;
    position: relative;
  }
  .card {
    position: absolute;
    width: 600px;
    height: 343px;
    left: 300px;
    overflow: hidden;
    box-shadow: 0 14px 30px rgba(0,0,0,.45);
  }
  /* Front */
  .card-front { top: 70px; background: var(--card-black); }
  .brand-mark {
    position: absolute;
    left: 0; right: 0; top: 118px;
    display: flex; align-items: center; justify-content: center; gap: 12px;
  }
  .brand-square { width: 18px; height: 18px; background: var(--green-mid); }
  .brand-name {
    color: var(--white);
    font-weight: 500;
    font-size: 30px;
    letter-spacing: 4px;
  }
  .front-rule {
    position: absolute;
    left: 90px; right: 90px; top: 218px;
    height: 2px;
    background: linear-gradient(90deg, transparent, var(--green-deep) 30%, var(--green-deep) 70%, transparent);
  }
  .front-web {
    position: absolute;
    left: 0; right: 0; top: 250px;
    text-align: center;
    color: var(--white);
    font-size: 17px;
    letter-spacing: 5px;
  }
  /* Back */
  .card-back {
    top: 470px;
    background: radial-gradient(circle at 48% 55%, var(--green-light) 0%, var(--green-mid) 45%, var(--green-deep) 100%);
  }
  .back-shape { position: absolute; inset: 0; }
  .person { position: absolute; right: 40px; top: 26px; text-align: right; }
  .person-name { color: var(--ink); font-weight: 700; font-size: 21px; letter-spacing: .5px; }
  .person-role { color: var(--white); font-size: 16px; margin-top: -2px; }
  .contact-list {
    position: absolute; left: 34px; top: 120px;
    list-style: none;
  }
  .contact-item {
    display: flex; align-items: center; gap: 10px;
    color: var(--white); font-size: 15.5px; line-height: 25px;
  }
  .contact-item svg { width: 14px; height: 14px; fill: var(--ink); flex: none; }
  .back-brand {
    position: absolute; left: 330px; top: 228px;
    display: flex; align-items: center; gap: 10px;
  }
  .back-brand .brand-name { font-size: 24px; letter-spacing: 3px; }
  .back-brand .brand-square { width: 16px; height: 16px; }
</style>
</head>
<body>

<section class="card card-front" aria-label="Card front">
  <div class="brand-mark">
    <span class="brand-square"></span>
    <span class="brand-name">TMW HOME CRAFTING</span>
  </div>
  <div class="front-rule"></div>
  <p class="front-web">www.tmwhomecrafting.com.au</p>
</section>

<section class="card card-back" aria-label="Card back">
  <svg class="back-shape" viewBox="0 0 600 343" preserveAspectRatio="none">
    <polygon points="95,343 352,122 600,150 600,343" fill="#1f9a45"/>
    <polygon points="130,343 362,148 600,176 600,343" fill="var(--card-black)"/>
  </svg>

  <div class="person">
    <p class="person-name">OWEN MARSH</p>
    <p class="person-role">General Manager</p>
  </div>

  <ul class="contact-list">
    <li class="contact-item">
      <svg viewBox="0 0 24 24"><path d="M6.6 10.8a15.1 15.1 0 0 0 6.6 6.6l2.2-2.2c.3-.3.7-.4 1-.2 1.1.4 2.3.6 3.6.6.6 0 1 .4 1 1V20c0 .6-.4 1-1 1C10.6 21 3 13.4 3 4c0-.6.4-1 1-1h3.5c.6 0 1 .4 1 1 0 1.3.2 2.5.6 3.6.1.3 0 .7-.2 1z"/></svg>
      0400 123 456
    </li>
    <li class="contact-item">
      <svg viewBox="0 0 24 24"><path d="M2 5h20v14H2z M2 5l10 8 10-8" fill="none" stroke="#0b0b0b" stroke-width="2"/></svg>
      info@tmwhomecrafting.com.au
    </li>
    <li class="contact-item">
      <svg viewBox="0 0 24 24"><circle cx="12" cy="12" r="9" fill="none" stroke="#0b0b0b" stroke-width="2"/><path d="M3 12h18M12 3c3 3 3 15 0 18M12 3c-3 3-3 15 0 18" fill="none" stroke="#0b0b0b" stroke-width="1.6"/></svg>
      www.tmwhomecrafting.com.au
    </li>
    <li class="contact-item">
      <svg viewBox="0 0 24 24"><path d="M12 2a7 7 0 0 0-7 7c0 5 7 13 7 13s7-8 7-13a7 7 0 0 0-7-7zm0 9.5A2.5 2.5 0 1 1 12 6.5a2.5 2.5 0 0 1 0 5z"/></svg>
      Riverton, Tasmania, Australia
    </li>
  </ul>

  <div class="back-brand">
    <span class="brand-square"></span>
    <span class="brand-name">TMW HOME CRAFTING</span>
  </div>
</section>

</body>
</html>
```